Modern corporate presentation

We need a clean, restrained company presentation in a modern Prezi style (design templates are attached for orientation). Please see the attachment for the briefing, colors and our corporate design.

content 1
Title:

FILOVAN
We connect worlds.
Digitization = increase in customer satisfaction

content 2
Animated on photo of company building (photo attached)

Text:

As Europe's leading service provider for business process outsourcing, we optimize your document management along the entire process chain of your document cycles, including physical long-term archiving after processing - efficiently, flexibly, individually and transparently!

content 3
Title: History
Overview of history as a timeline (see example design template slide 2) with dates and icons
Text:
1995
1997
2000
2016
2018
2021

content 4 or onwards
Morph transitions / individual seasons
1995 Founded by Lothar Brenner
1997 Start of ARKI@NET development
2000 real start ARKI@NET, certification GoB/S and KVR
2016 Development of Big Data + inMemory searches, first processes with AI
2018
ARKI@NET goes mobile
Expansion of the Siegen site with a new logistics center
Launch Papyrix concept
2021 More than 400 satisfied employees

content 5
Title: Facts and Figures
Animated to morph the following texts/numbers:

family business
400 employees at different locations
Own data centers
7,500 pallet spaces
50,000 active users daily on the ARKI@NET platform
525 000 receipts per month
210 customers from all over Europe
all necessary certifications

content 6
Title: Product and service portfolio
Combine yourself...
Create animation from Lego building blocks, which are put together, morph individually according to the order (1-3).

Module 1:
system platform
• Audit-proof archiving ARKI@NET
• Fully integrated document management
• Complete, certified KVR® integration

Module 2:
solution modules
• Digital files
• Invoice receipt workflow
ordering system
• Digital inbox
• Case management
• Data Lantern

Module 3:

process services
• Storage
• Scanning Service
• Collection Services
• BPO Inbox
• BPO invoice receipt

content 7
Title: Good Reasons / Benefits
Trust / full-service provider for document-based business processes completely own solution
Portfolio / depiction of the entire process chain from a single source
Experience / reference projects of all sizes and industries
Employees / All services are provided by our own staff without the involvement of subcontractors

content 8
Title: The 100% Philosophy

Overview of the following 3 main points, which are highlighted individually below:

The system
Services
Privacy and Certifications
___

The system
• 100% own data center with 24x7 operation, incl. backup data center
• Certified KVR partner
• Real, completely in-house developed SaaS solution for data center operations only
• Maintenance, support and updates included
• Web-based application

Services
• Combination of man & machine
• Service level agreements, service defined in terms of time
• Penalty for non-fulfilment

Privacy and certifications:
• All common certifications
• Own compliance management
• Data protection according to GDPR

Font styles to use
Other font styles liked:
• Myrlad Pro Bold für Head und Sublines, Lucida Grande Regular für Fließtexte

Requirements
Must have
• clean and reserved, taking our corporate design into account
Nice to have
• Prezi Style, seamless transitions (similar to a scrollipage)

```html
<!DOCTYPE html>
<html lang="en">
<head>
<meta charset="utf-8">
<title>FILOVAN – Company Presentation</title>
<link href="https://fonts.googleapis.com/css2?family=Montserrat:wght@300;400;500;600;700&display=swap" rel="stylesheet">
<style>
:root{
  --stage:#9b9b9b;
  --slide:#f1f1f1;
  --slide-light:#fafafa;
  --ink:#1f1f1f;
  --muted:#7a7a7a;
  --slate:#6b8196;
  --sand:#cfc5a5;
  --white:#ffffff;
  --photo-dark:#1e2836;
  --photo-mid:#3d4b5e;
}
*{box-sizing:border-box;margin:0;padding:0}
html,body{width:1200px;height:4082px;overflow:hidden}
body{background:var(--stage);font-family:"Montserrat",sans-serif;color:var(--ink);position:relative}
.slide{position:absolute;left:90px;width:1020px;height:574px;overflow:hidden;
  background:linear-gradient(125deg,var(--slide-light) 0%,var(--slide) 45%,#e9e9e9 70%,var(--slide-light) 100%)}
.slide--title{top:89px}
.slide--mission{top:756px}
.slide--history{top:1423px}
.slide--philosophy{top:2090px}
.slide--facts{top:2757px}
.slide--portfolio{top:3424px}

.brand{position:absolute;top:18px;right:26px;display:flex;align-items:center;gap:6px;
  font-family:"Montserrat",sans-serif;font-weight:400;font-size:25px;letter-spacing:0.5px;color:#3a3a3a}
.brand__mark{width:22px;height:20px;background:#3a3a3a;border-radius:3px}

.slide-title{position:absolute;left:0;right:0;text-align:center;font-weight:700;font-size:35px;letter-spacing:0.5px;line-height:48px}

/* Title slide */
.hero-brand{position:absolute;left:57px;top:255px;display:flex;align-items:center;gap:18px;
  font-weight:300;font-size:74px;letter-spacing:2px;color:#333;line-height:1}
.hero-brand__mark{width:58px;height:54px;background:#333;border-radius:7px}
.hero-divider{position:absolute;left:518px;top:176px;width:6px;height:222px;
  background:linear-gradient(var(--sand) 0 50%,var(--slate) 50% 100%)}
.hero-copy{position:absolute;left:568px;top:190px}
.hero-copy h1{font-size:50px;font-weight:700;letter-spacing:1px;line-height:60px}
.hero-copy h2{font-size:28px;font-weight:700;letter-spacing:0.5px;margin-top:2px}
.hero-copy p{font-size:17px;font-weight:600;line-height:31px;margin-top:12px;width:360px}

/* Mission slide */
.photo-building{position:absolute;inset:0;
  background:linear-gradient(180deg,#2b3a52 0%,var(--photo-mid) 30%,#3a4250 55%,#2a3038 75%,var(--photo-dark) 100%)}
.mission-band{position:absolute;left:0;right:0;top:170px;height:248px;background:rgba(20,24,30,0.62);
  display:flex;align-items:center;justify-content:center}
.mission-band p{width:800px;text-align:center;color:var(--white);font-weight:700;font-size:17px;line-height:31px}
.slide--mission .brand{color:rgba(255,255,255,0.25)}
.slide--mission .brand__mark{background:rgba(255,255,255,0.25)}

/* History */
.timeline{position:absolute;left:0;top:315px}
.timeline text{font-family:"Montserrat",sans-serif;font-weight:700;font-size:14px;fill:var(--white)}
.milestone{position:absolute;width:220px;margin-left:-110px;text-align:center}
.milestone h3{font-size:15px;font-weight:600;line-height:20px}
.milestone p{font-size:9.5px;color:var(--muted);line-height:15.5px;margin-top:4px}
.milestone--up{top:170px}
.milestone--down{top:412px}
.connector{position:absolute;width:0;border-left:2px dotted #b9b9b9}
.connector--up{top:256px;height:40px}
.connector--down{top:365px;height:36px}
.connector::after{content:"";position:absolute;left:-4px;width:6px;height:6px;border-radius:50%}
.connector--up::after{bottom:-2px;background:var(--sand)}
.connector--down::after{top:-3px;background:var(--slate)}

/* Cards */
.card{position:absolute;width:242px}
.card__image{height:195px;border-top-right-radius:46px}
.card__label{position:relative;height:58px;background:var(--white);border-radius:0 0 14px 14px;
  box-shadow:0 6px 12px rgba(0,0,0,0.08);display:flex;flex-direction:column;align-items:center;justify-content:center;text-align:center}
.card__label h3{font-size:16.5px;font-weight:700;line-height:20px}
.card__label span{font-size:9.5px;color:#555;margin-top:2px}
.card__list{list-style:none;margin-top:20px;text-align:center;font-size:10.5px;line-height:22px;color:#444;padding:0 4px}
.card--a{left:83px}
.card--b{left:389px}
.card--c{left:693px}
.slide--philosophy .card{top:119px}
.slide--portfolio .card{top:178px}

.img-office{background:linear-gradient(150deg,#4a4f55 0%,#8b8f94 45%,#d8d6d2 75%,#eeeeec 100%)}
.img-servers{background:linear-gradient(180deg,#0b2a44 0%,#1f6c9e 45%,#4fb4e0 60%,#123c5e 100%)}
.img-lock{background:radial-gradient(circle at 45% 50%,#c9e6ff 0%,#4a8fd6 30%,#1d4f9c 65%,#0c2450 100%)}
.img-team{background:linear-gradient(140deg,#5a3b2a 0%,#8c6a55 35%,#c9c2b8 70%,#e3e0dc 100%)}
.img-tablet{background:linear-gradient(150deg,#253447 0%,#6d8aa8 45%,#c7d3df 75%,#e6ecf2 100%)}
.img-hands{background:radial-gradient(circle at 50% 55%,#5f6f7e 0%,#2c343c 45%,#121518 100%)}

/* Facts */
.facts-band{position:absolute;left:0;right:0;top:166px;height:316px;background:var(--slate)}
.facts-band h3{position:absolute;top:30px;left:0;right:0;text-align:center;color:#e7e0c9;font-size:15px;font-weight:600;letter-spacing:0.5px}
.fact{position:absolute;top:94px;width:140px;height:140px;margin-left:-70px;border-radius:50%;background:var(--white);
  border:4px solid var(--sand);box-shadow:0 0 0 3px rgba(255,255,255,0.5);
  display:flex;flex-direction:column;align-items:center;justify-content:center;text-align:center;padding:0 16px}
.fact strong{font-size:25px;font-weight:600;color:var(--slate);line-height:30px}
.fact span{font-size:6.8px;font-weight:700;line-height:11px;margin-top:6px;text-transform:uppercase}
</style>
</head>
<body>

<section class="slide slide--title">
  <div class="brand"><span class="brand__mark"></span>FILOVAN</div>
  <div class="hero-brand"><span class="hero-brand__mark"></span>FILOVAN</div>
  <div class="hero-divider"></div>
  <div class="hero-copy">
    <h1>FILOVAN</h1>
    <h2>WE CONNECT WORLDS.</h2>
    <p>Digitization = increase in customer satisfaction</p>
  </div>
</section>

<section class="slide slide--mission">
  <div class="photo-building" role="img" aria-label="Photo of the company building at dusk reflected in water"></div>
  <div class="brand"><span class="brand__mark"></span>FILOVAN</div>
  <div class="mission-band">
    <p>As Europe's leading service provider for business process outsourcing, we optimize your document management along the entire process chain of your document cycles, in&shy;cluding physical long-term archiving after processing - efficiently, flexibly, individually and transparently!</p>
  </div>
</section>

<section class="slide slide--history">
  <div class="brand"><span class="brand__mark"></span>FILOVAN</div>
  <h2 class="slide-title" style="top:31px">HISTORY</h2>

  <div class="milestone milestone--up" style="left:292px"><h3>Lorem Ipsum</h3><p>Lorem ipsum dolor sit amet, consectetur adipisc&shy;ing elit, sed do eiusmod tempor incididunt ut labore et dolore magna aliqua.</p></div>
  <div class="milestone milestone--up" style="left:580px"><h3>Lorem Ipsum</h3><p>Lorem ipsum dolor sit amet, consectetur adipisc&shy;ing elit, sed do eiusmod tempor incididunt ut labore et dolore magna aliqua.</p></div>
  <div class="milestone milestone--up" style="left:869px"><h3>Lorem Ipsum</h3><p>Lorem ipsum dolor sit amet, consectetur adip&shy;iscing elit, sed do eiusmod tempor incididunt ut labore et dolore magna aliqua.</p></div>
  <div class="connector connector--up" style="left:291px"></div>
  <div class="connector connector--up" style="left:579px"></div>
  <div class="connector connector--up" style="left:868px"></div>

  <svg class="timeline" width="1020" height="34" viewBox="0 0 1020 34">
    <polygon points="75,0 219,0 233,17 219,34 75,34 89,17" fill="#6b8196"/>
    <polygon points="219,0 363,0 377,17 363,34 219,34 233,17" fill="#cfc5a5"/>
    <polygon points="363,0 507,0 521,17 507,34 363,34 377,17" fill="#6b8196"/>
    <polygon points="507,0 651,0 665,17 651,34 507,34 521,17" fill="#cfc5a5"/>
    <polygon points="651,0 795,0 809,17 795,34 651,34 665,17" fill="#6b8196"/>
    <polygon points="795,0 939,0 953,17 939,34 795,34 809,17" fill="#cfc5a5"/>
    <text x="154" y="22" text-anchor="middle">1995</text>
    <text x="298" y="22" text-anchor="middle">1997</text>
    <text x="442" y="22" text-anchor="middle">2000</text>
    <text x="586" y="22" text-anchor="middle">2016</text>
    <text x="730" y="22" text-anchor="middle">2018</text>
    <text x="874" y="22" text-anchor="middle">2021</text>
  </svg>

  <div class="connector connector--down" style="left:145px"></div>
  <div class="connector connector--down" style="left:433px"></div>
  <div class="connector connector--down" style="left:722px"></div>
  <div class="milestone milestone--down" style="left:146px"><h3>Lorem Ipsum</h3><p>Lorem ipsum dolor sit amet, consectetur adipiscing elit, sed do eiusmod tempor incididunt ut labore et dolore magna aliqua. Quis ipsum suspendisse ul&shy;trices gravida.</p></div>
  <div class="milestone milestone--down" style="left:434px"><h3>Lorem Ipsum</h3><p>Lorem ipsum dolor sit amet, consectetur adipiscing elit, sed do eiusmod tempor incididunt ut labore et dolore magna aliqua. Quis ipsum suspendisse ul&shy;trices gravida.</p></div>
  <div class="milestone milestone--down" style="left:723px"><h3>Lorem Ipsum</h3><p>Lorem ipsum dolor sit amet, consectetur adipisc&shy;ing elit, sed do eiusmod tempor incididunt ut labore et dolore magna aliqua. Quis ipsum suspen&shy;disse ultrices gravida.</p></div>
</section>

<section class="slide slide--philosophy">
  <div class="brand"><span class="brand__mark"></span>FILOVAN</div>
  <h2 class="slide-title" style="top:31px">THE 100% PHILOSOPHY</h2>

  <article class="card card--a">
    <div class="card__image img-office" role="img" aria-label="Photo of hands working on a laptop with digital documents"></div>
    <div class="card__label"><h3>THE SYSTEM</h3></div>
    <ul class="card__list">
      <li>•100% own data center with 24x7 operation, incl. backup data center</li>
      <li>• Certified KVR partner</li>
      <li>• Real, fully self-developed SaaS solution for data center operations only</li>
      <li>• Maintenance, support and updates included</li>
      <li>• Web-based application</li>
    </ul>
  </article>

  <article class="card card--b">
    <div class="card__image img-servers" role="img" aria-label="Photo of a lit data center server aisle"></div>
    <div class="card__label"><h3>SERVICES</h3></div>
    <ul class="card__list">
      <li>•Combination of man &amp; machine</li>
      <li>• Service level agreements, service defined in terms of time</li>
      <li>• Penalty for non-fulfilment</li>
    </ul>
  </article>

  <article class="card card--c">
    <div class="card__image img-lock" role="img" aria-label="Illustration of a glowing padlock above an open hand"></div>
    <div class="card__label"><h3>PRIVACY AND<br>CERTIFICATIONS</h3></div>
    <ul class="card__list">
      <li>• Storage</li>
      <li>• Scanning Service</li>
      <li>• Collection Services</li>
      <li>• BPO Inbox</li>
      <li>• BPO invoice receipt</li>
    </ul>
  </article>
</section>

<section class="slide slide--facts">
  <div class="brand"><span class="brand__mark"></span>FILOVAN</div>
  <h2 class="slide-title" style="top:54px">FACTS AND FIGURES</h2>
  <div class="facts-band">
    <h3>FAMILY BUSINESS</h3>
    <div class="fact" style="left:119px"><strong>400</strong><span>Employees at different locations own data centers</span></div>
    <div class="fact" style="left:316px"><strong>7,500</strong><span>Pallet spaces</span></div>
    <div class="fact" style="left:511px"><strong>50,000</strong><span>Active users daily on the ARKI@NET platform</span></div>
    <div class="fact" style="left:706px"><strong>525 000</strong><span>Receipts per month</span></div>
    <div class="fact" style="left:902px"><strong>210</strong><span>Customers from all over Europe</span></div>
  </div>
</section>

<section class="slide slide--portfolio">
  <div class="brand"><span class="brand__mark"></span>FILOVAN</div>
  <h2 class="slide-title" style="top:27px">PRODUCT AND SERVICE<br>PORTFOLIO</h2>

  <article class="card card--a">
    <div class="card__image img-team" role="img" aria-label="Photo of two colleagues working together at a computer"></div>
    <div class="card__label"><h3>SYSTEM PLATFORM</h3><span>Module 1</span></div>
    <ul class="card__list">
      <li>• Audit-proof archiving ARKI@NET</li>
      <li>• Fully integrated document management</li>
      <li>• Complete, certified KVR® integration</li>
    </ul>
  </article>

  <article class="card card--b">
    <div class="card__image img-tablet" role="img" aria-label="Photo of hands using a tablet with digital interface graphics"></div>
    <div class="card__label"><h3>SOLUTION MODULES</h3><span>Module 2</span></div>
    <ul class="card__list">
      <li>•Digital files</li>
      <li>• Invoice receipt workflow ordering system</li>
      <li>• Digital inbox</li>
      <li>• Case management</li>
      <li>• Data Lantern</li>
    </ul>
  </article>

  <article class="card card--c">
    <div class="card__image img-hands" role="img" aria-label="Photo of open hands holding a glowing digital object"></div>
    <div class="card__label"><h3>PROCESS SERVICES</h3><span>Module 3</span></div>
    <ul class="card__list">
      <li>• Storage</li>
      <li>• Scanning Service</li>
      <li>• Collection Services</li>
      <li>• BPO Inbox</li>
      <li>• BPO invoice receipt</li>
    </ul>
  </article>
</section>

</body>
</html>
```